Oil and Gas Exploration and Production company needs a business card design

We need a business card design using our logo and colors in the logo. We want a mainstream design.

```html
<!DOCTYPE html>
<html lang="en">
<head>
<meta charset="utf-8">
<title>Condor Oil &amp; Gas – Business Card</title>
<link rel="stylesheet" href="https://fonts.googleapis.com/css2?family=Open+Sans:wght@400;600;700;800&display=swap">
<style>
  :root {
    --backdrop: #4a423d;
    --card: #141414;
    --card-edge: #1d1d1d;
    --gold: #d9a033;
    --white: #f4f4f4;
    --grey: #9a9a9a;
    --divider: #5c5c5c;
  }
  * { box-sizing: border-box; margin: 0; padding: 0; }
  html, body {
    width: 1200px; height: 864px; overflow: hidden;
    background: var(--backdrop);
    font-family: "Open Sans", Arial, sans-serif;
  }
  .stage {
    width: 1200px; height: 864px;
    display: flex; align-items: center; justify-content: center; gap: 40px;
  }
  .card {
    width: 540px; height: 309px;
    background: linear-gradient(135deg, var(--card-edge), var(--card));
    box-shadow: 0 14px 30px rgba(0,0,0,.45);
    position: relative;
    color: var(--white);
  }
  .brand { display: flex; align-items: center; gap: 12px; }
  .brand-dot {
    width: 30px; height: 30px; border-radius: 50%;
    background: var(--gold); flex: none;
  }
  .brand-name {
    font-weight: 800; color: var(--white); line-height: 1.02;
    letter-spacing: .5px;
  }
  .brand-name span { display: block; }

  /* front */
  .card-front {
    display: flex; flex-direction: column; align-items: center; justify-content: center;
  }
  .card-front .brand-name { font-size: 46px; }
  .card-front .brand-dot { width: 38px; height: 38px; }
  .front-web {
    margin-top: 28px; font-size: 13px; letter-spacing: 4px; color: var(--grey);
  }

  /* back */
  .card-back { display: flex; align-items: center; }
  .card-back .brand { width: 270px; padding-left: 34px; }
  .card-back .brand-name { font-size: 36px; }
  .back-divider {
    width: 1px; height: 200px;
    background: linear-gradient(transparent, var(--divider), transparent);
  }
  .contact { padding-left: 22px; font-size: 12.5px; line-height: 1.45; }
  .contact-name { color: var(--gold); font-weight: 700; font-size: 15px; letter-spacing: .5px; }
  .contact-role { font-size: 12px; margin-bottom: 4px; letter-spacing: .5px; }
  .contact-address { margin-bottom: 4px; }
  .contact-line { display: flex; align-items: center; gap: 8px; }
  .contact-line svg { width: 12px; height: 12px; fill: var(--gold); flex: none; }
  .contact-line.plain { padding-left: 20px; }
</style>
</head>
<body>
<main class="stage">
  <section class="card card-front">
    <div class="brand">
      <div class="brand-dot"></div>
      <div class="brand-name"><span>Condor</span><span>Oil &amp; Gas</span></div>
    </div>
    <p class="front-web">www.condoroilgas.com</p>
  </section>

  <section class="card card-back">
    <div class="brand">
      <div class="brand-dot"></div>
      <div class="brand-name"><span>Condor</span><span>Oil &amp; Gas</span></div>
    </div>
    <div class="back-divider"></div>
    <div class="contact">
      <p class="contact-name">MARK ELLISON</p>
      <p class="contact-role">PRESIDENT</p>
      <p class="contact-address">2190 Harlow Avenue<br>Cedar Bluff, NY 11204</p>
      <p class="contact-line">
        <svg viewBox="0 0 12 12" aria-hidden="true"><path d="M2.5 1 4.5 1 5.3 3.6 4 4.6C4.6 6 5.8 7.3 7.4 8L8.4 6.7 11 7.5 11 9.5C11 10.3 10.3 11 9.5 11 5 11 1 7 1 2.5 1 1.7 1.7 1 2.5 1Z"/></svg>
        555 0142 7731
      </p>
      <p class="contact-line">
        <svg viewBox="0 0 12 12" aria-hidden="true"><path d="M3 1h6v3H3zM1 5h10v4H9v2H3V9H1zM4 8v2h4V8z"/></svg>
        555 0198 2460
      </p>
      <p class="contact-line">
        <svg viewBox="0 0 12 12" aria-hidden="true"><path d="M3.5 0.5h5a1 1 0 0 1 1 1v9a1 1 0 0 1-1 1h-5a1 1 0 0 1-1-1v-9a1 1 0 0 1 1-1zM4 2v7h4V2z"/></svg>
        555 0175 3904
      </p>
      <p class="contact-line">
        <svg viewBox="0 0 12 12" aria-hidden="true"><path d="M1 2.5h10v7H1zM1.6 3 6 6.4 10.4 3"/></svg>
        info@condoroilgas.com
      </p>
      <p class="contact-line">
        <svg viewBox="0 0 12 12" aria-hidden="true"><circle cx="6" cy="6" r="5"/></svg>
        www.condoroilgas.com
      </p>
    </div>
  </section>
</main>
</body>
</html>
```